Create modern and sleek business card for luxury real estate company

We're a "boutique" real estate office looking for a design that gets across a highly modern luxury brand. Blacks and whites are probably the best colors unless we try a silver foil for the logo. I've attached a version of our current logo here. I'd like to swap out the current font on there with Gotham Light Regular.

I'm looking to have one side of the card have the logo with the space for our agents info on the other side.

Target Market(s)

Young professionals in a "luxury" headspace

Industry/Entity Type

Real estate

Contact Information for Business Card

A place for agent name, cell number, website. The slogan "Simply Rethinking Real Estate".

Font styles to use
Other font styles liked:
• Gotham Regular

Colors

Designer to choose only greyscale colors for use in the design.

Requirements
Must have
• Matte black as the background color. Clean lines and use of contrast. A specific design aspect that will use silver foil.
Nice to have
• Up in the air on integrating a QR code
Should not have
• Any houses or other real estate related design (ex: a clip art house)

```html
<!DOCTYPE html>
<html lang="en">
<head>
<meta charset="utf-8">
<title>Halden Realty — Business Card</title>
<link href="https://fonts.googleapis.com/css2?family=Montserrat:wght@300;400;600&display=swap" rel="stylesheet">
<style>
  :root {
    --canvas: #eef0f0;
    --matte-black: #050505;
    --deep-black: #0d0d0d;
    --ring-silver: #a9a9a9;
    --ring-shade: #6e6e6e;
    --foil: #dcdcdc;
    --paper: #ffffff;
    --ink: #111111;
    --faint: #1b1b1b;
  }
  * { box-sizing: border-box; margin: 0; padding: 0; }
  html, body { width: 1200px; height: 1200px; overflow: hidden; }
  body {
    background: var(--canvas);
    font-family: "Montserrat", sans-serif;
    position: relative;
  }
  .card {
    position: absolute;
    top: 453px;
    width: 520px;
    height: 294px;
    overflow: hidden;
    box-shadow: 0 10px 22px rgba(0,0,0,0.28);
  }
  .card--front { left: 50px; background: var(--paper); }
  .card--back { left: 630px; background: var(--matte-black); }

  .front-art { position: absolute; inset: 0; }

  .brand {
    position: absolute;
    display: flex;
    align-items: center;
    gap: 10px;
    color: var(--foil);
  }
  .brand__dot {
    width: 34px; height: 34px;
    border: 2px solid var(--foil);
    border-radius: 50%;
    flex: none;
  }
  .brand__name {
    font-weight: 400;
    font-size: 19px;
    line-height: 1.05;
    letter-spacing: 1px;
    text-transform: uppercase;
  }
  .brand__name span { display: block; }
  .brand__name span + span {
    border-top: 1.5px solid var(--foil);
    padding-top: 2px;
    margin-top: 2px;
    padding-left: 10px;
  }
  .card--front .brand { left: 34px; top: 112px; }
  .card--back .brand { left: 50%; top: 50%; transform: translate(-50%, -50%); }

  .agent {
    position: absolute;
    left: 312px;
    top: 106px;
    right: 0;
    color: var(--ink);
  }
  .agent__name { font-weight: 600; font-size: 12px; letter-spacing: 0.3px; }
  .agent__role { font-weight: 400; font-size: 10px; letter-spacing: 0.3px; }
  .agent__rule { height: 3px; background: var(--ink); margin: 5px 0 8px; }
  .agent__line {
    display: flex; align-items: center; gap: 7px;
    font-size: 11px; font-weight: 400; margin-bottom: 6px;
  }
  .agent__line svg { width: 11px; height: 11px; flex: none; }

  .monogram-field {
    position: absolute; inset: 0;
    background: radial-gradient(ellipse at center, #141414 0%, #0a0a0a 70%, #050505 100%);
  }
</style>
</head>
<body>
  <section class="card card--front" aria-label="Business card front">
    <svg class="front-art" viewBox="0 0 520 294" width="520" height="294" aria-hidden="true">
      <defs>
        <linearGradient id="ringGrad" x1="0" y1="0" x2="0" y2="1">
          <stop offset="0" stop-color="var(--ring-shade)"/>
          <stop offset="0.5" stop-color="var(--ring-silver)"/>
          <stop offset="1" stop-color="var(--ring-shade)"/>
        </linearGradient>
      </defs>
      <circle cx="30" cy="147" r="238" fill="url(#ringGrad)"/>
      <circle cx="22" cy="147" r="226" fill="var(--matte-black)"/>
      <circle cx="90" cy="150" r="128" fill="none" stroke="var(--faint)" stroke-width="10"/>
    </svg>
    <div class="brand">
      <div class="brand__dot"></div>
      <div class="brand__name"><span>Halden</span><span>Realty</span></div>
    </div>
    <div class="agent">
      <p class="agent__name">DANIEL REYES</p>
      <p class="agent__role">DESIGNER</p>
      <div class="agent__rule"></div>
      <p class="agent__line">
        <svg viewBox="0 0 24 24"><path fill="#111" d="M6.6 10.8a15.2 15.2 0 0 0 6.6 6.6l2.2-2.2a1 1 0 0 1 1-.25 11.4 11.4 0 0 0 3.6.57 1 1 0 0 1 1 1V20a1 1 0 0 1-1 1A17 17 0 0 1 3 4a1 1 0 0 1 1-1h3.5a1 1 0 0 1 1 1c0 1.25.2 2.45.57 3.6a1 1 0 0 1-.25 1z"/></svg>
        555-014-2290
      </p>
      <p class="agent__line">
        <svg viewBox="0 0 24 24"><circle cx="12" cy="12" r="10" fill="#111"/><path d="M2.5 12h19M12 2.5c3 3 3 16 0 19M12 2.5c-3 3-3 16 0 19" stroke="#fff" stroke-width="1.4" fill="none"/></svg>
        www.haldenrealty.com
      </p>
    </div>
  </section>

  <section class="card card--back" aria-label="Business card back">
    <div class="monogram-field" role="img" aria-label="Subtle tone-on-tone repeating brand monogram pattern"></div>
    <div class="brand">
      <div class="brand__dot"></div>
      <div class="brand__name"><span>Halden</span><span>Realty</span></div>
    </div>
  </section>
</body>
</html>
```